At Home Pet Euthanasia - business cards & brand stationary

We already have a logo and the colors and a website. Need a business card designed that will be able to customized to multiple veterinarians who will be partnering with us. The feel needs to be compassionate, comforting with our tagline 'A Gift of Love at Home'. It will be 2 sides.
On the back our platform/partner vets will be customizing each business card with their own service areas, phone numbers, name and title. On the front, i would like to see experimentation with use of our photos, the logo, tagline and a description 'Peaceful and Compassionate At-Home Pet Euthanasia'

```html
<!DOCTYPE html>
<html lang="en">
<head>
<meta charset="utf-8">
<title>Willowrest – Business Cards</title>
<link rel="stylesheet" href="https://fonts.googleapis.com/css2?family=Arimo:wght@400;700&family=Raleway:wght@300;400&display=swap">
<style>
  :root {
    --backdrop: #2e2f31;
    --card: #7799c0;
    --card-tint: #81a3cb;
    --ink: #ffffff;
    --rule: rgba(255,255,255,0.55);
  }
  * { margin: 0; padding: 0; box-sizing: border-box; }
  html, body { width: 1200px; height: 1015px; overflow: hidden; }
  body {
    background: var(--backdrop);
    font-family: "Arimo", Arial, sans-serif;
    color: var(--ink);
    position: relative;
  }
  .card {
    position: absolute;
    left: 220px;
    width: 760px;
    height: 434px;
    background: var(--card);
    box-shadow: 0 10px 28px rgba(0,0,0,0.45);
  }
  .card--front { top: 50px; }
  .card--back { top: 531px; }

  /* Front */
  .brand {
    position: absolute;
    left: 160px;
    top: 108px;
    display: flex;
    align-items: center;
    gap: 22px;
  }
  .brand__mark {
    width: 34px; height: 34px;
    border-radius: 50%;
    background: var(--ink);
  }
  .brand__name {
    font-family: "Arimo", Arial, sans-serif;
    font-weight: 700;
    font-size: 84px;
    letter-spacing: -1px;
    line-height: 1;
  }
  .brand__tagline {
    position: absolute;
    left: 330px;
    top: 208px;
    font-family: "Raleway", Arial, sans-serif;
    font-weight: 400;
    font-size: 26px;
    letter-spacing: 0.5px;
  }
  .service-line {
    position: absolute;
    left: 40px;
    right: 40px;
    bottom: 64px;
    border-top: 1px solid var(--rule);
    padding-top: 10px;
    font-size: 20.5px;
    letter-spacing: 1.1px;
    text-transform: uppercase;
    white-space: nowrap;
  }

  /* Back */
  .contact {
    position: absolute;
    left: 70px;
    top: 120px;
  }
  .contact__name {
    font-weight: 700;
    font-size: 29px;
    letter-spacing: 0.5px;
    text-transform: uppercase;
  }
  .contact__title {
    font-size: 19px;
    letter-spacing: 0.8px;
    text-transform: uppercase;
    margin-top: 2px;
  }
  .contact__list {
    list-style: none;
    margin-top: 36px;
    font-size: 22px;
    line-height: 30px;
  }
  .contact__list li { display: flex; align-items: center; gap: 10px; }
  .contact__list svg { width: 20px; height: 20px; flex: none; }
  .contact__address {
    margin-top: 40px;
    font-size: 22px;
    line-height: 28px;
    font-style: normal;
  }
  .emboss-block {
    position: absolute;
    right: 70px;
    top: 70px;
    width: 260px;
    height: 260px;
    background: var(--card-tint);
    border-radius: 10px;
    box-shadow: inset 1px 1px 2px rgba(255,255,255,0.25), inset -1px -1px 2px rgba(0,0,0,0.12);
  }
</style>
</head>
<body>
  <section class="card card--front" aria-label="Business card front">
    <div class="brand">
      <span class="brand__mark" aria-hidden="true"></span>
      <span class="brand__name">Willowrest</span>
    </div>
    <p class="brand__tagline">A gift of love at home.</p>
    <p class="service-line">Peaceful and compassionate at-home pet euthanasia</p>
  </section>

  <section class="card card--back" aria-label="Business card back">
    <div class="contact">
      <h1 class="contact__name">Daniel Hart</h1>
      <p class="contact__title">Managing Director</p>
      <ul class="contact__list">
        <li>
          <svg viewBox="0 0 24 24" aria-hidden="true"><path fill="#fff" d="M6.6 10.8a15.1 15.1 0 0 0 6.6 6.6l2.2-2.2a1 1 0 0 1 1-.25 11.4 11.4 0 0 0 3.6.57 1 1 0 0 1 1 1V20a1 1 0 0 1-1 1A17 17 0 0 1 3 4a1 1 0 0 1 1-1h3.5a1 1 0 0 1 1 1c0 1.25.2 2.45.57 3.57a1 1 0 0 1-.25 1z"/></svg>
          055-987 654 321
        </li>
        <li>
          <svg viewBox="0 0 24 24" aria-hidden="true"><rect x="2" y="5" width="20" height="14" fill="none" stroke="#fff" stroke-width="2"/><path d="M2 5l10 8 10-8" fill="none" stroke="#fff" stroke-width="2"/></svg>
          hello@willowrest.com
        </li>
        <li>
          <svg viewBox="0 0 24 24" aria-hidden="true"><circle cx="12" cy="12" r="9.5" fill="none" stroke="#fff" stroke-width="2"/><ellipse cx="12" cy="12" rx="4" ry="9.5" fill="none" stroke="#fff" stroke-width="1.6"/><path d="M2.5 12h19M4 7h16M4 17h16" stroke="#fff" stroke-width="1.4"/></svg>
          www.willowrest.com
        </li>
      </ul>
      <address class="contact__address">421, Address line goes here<br>45452, Country Name</address>
    </div>
    <div class="emboss-block" aria-hidden="true"></div>
  </section>
</body>
</html>
```